Modern Business Card for Larkwell 2018

Our company assumes the best about people. We are creating an online community of entrepreneurs and business leaders who struggle with marketing their business online.

This business card should POP! We recently got a new logo and are launching a new website next month, so our business cards should make a statement that feels:
-Fresh
-Smart
-Trustworthy
-Fun

Target Market(s)

small business owners, entrepreneurs

Industry/Entity Type

Digital Marketing

Contact Information for Business Card

Dimensions: 3.5" x 2"

Font styles to use
Sans Serif

Colors
f37122
ffffff

Requirements
Must have
• We need a business card with a modern, bold design. We will use one side of the card as a lead-generation offer, so text on one side will need to fit up to 140 characters. The business card should stick to our core colors (orange, black, and white).
Nice to have
• We think a vertical "portrait" design could be interesting.
Should not have
• Should not look like a traditional business card. The round icon should stand out from a distance.

```html
<!DOCTYPE html>
<html lang="en">
<head>
<meta charset="UTF-8">
<title>Larkwell Business Card</title>
<link href="https://fonts.googleapis.com/css2?family=Roboto:wght@400;500;700&family=Roboto+Condensed:wght@700&display=swap" rel="stylesheet">
<style>
  :root {
    --brand-orange: #f36a27;
    --paper-white: #f2f2f2;
    --pure-white: #ffffff;
    --ink-dark: #222222;
    --ink-grey: #555555;
    --backdrop: #242424;
  }
  * { margin: 0; padding: 0; box-sizing: border-box; }
  html, body { width: 1200px; height: 960px; overflow: hidden; background: var(--backdrop); }
  .canvas { position: relative; width: 1200px; height: 960px; font-family: "Roboto", sans-serif; }

  .card { position: absolute; width: 600px; height: 343px; }

  /* Front */
  .card-front { left: 314px; top: 113px; background: var(--paper-white); }
  .front-brand { position: absolute; right: 38px; top: 34px; display: flex; flex-direction: column; align-items: center; gap: 10px; }
  .front-brand-dot { width: 104px; height: 104px; border-radius: 50%; background: var(--brand-orange); }
  .front-brand-name { font-weight: 700; font-size: 18px; letter-spacing: 2px; color: var(--brand-orange); }
  .person-name { position: absolute; left: 36px; top: 241px; font-family: "Roboto Condensed", sans-serif; font-weight: 700; font-size: 25px; color: var(--brand-orange); letter-spacing: 0.2px; }
  .person-details { position: absolute; left: 38px; top: 281px; display: flex; align-items: center; }
  .person-role { font-size: 16px; font-weight: 500; color: var(--ink-dark); letter-spacing: 0.2px; }
  .detail-divider { width: 1px; height: 18px; background: var(--ink-dark); margin: 0 20px 0 19px; }
  .person-email { font-size: 15px; color: var(--ink-grey); }

  /* Back */
  .card-back { left: 311px; top: 472px; background: var(--brand-orange); color: var(--pure-white); }
  .back-brand { position: absolute; left: 0; top: 58px; width: 297px; display: flex; flex-direction: column; align-items: center; }
  .back-brand-dot { width: 36px; height: 36px; border-radius: 50%; background: var(--pure-white); }
  .back-brand-name { margin-top: 12px; font-weight: 700; font-size: 40px; letter-spacing: 2.5px; line-height: 1; }
  .back-tagline { margin-top: 7px; font-family: "Roboto Condensed", sans-serif; font-weight: 700; font-size: 12px; letter-spacing: 1.4px; }
  .back-divider { position: absolute; left: 297px; top: 25px; width: 1px; height: 166px; background: rgba(255,255,255,0.55); }
  .offer { position: absolute; left: 323px; top: 28px; width: 270px; }
  .offer-headline { font-weight: 700; font-size: 19.5px; line-height: 21px; letter-spacing: 0.2px; }
  .offer-body { margin-top: 5px; font-size: 15.5px; line-height: 20px; }
  .offer-link { margin-top: 6px; font-weight: 700; font-size: 20px; }
  .notes-box { position: absolute; left: 20px; top: 217px; width: 557px; height: 102px; background: var(--pure-white); border-radius: 18px; }
  .notes-line { position: absolute; left: 24px; right: 27px; height: 1px; background: var(--ink-dark); }
  .notes-line.first { top: 31px; }
  .notes-line.second { top: 71px; }
</style>
</head>
<body>
<main class="canvas">
  <section class="card card-front">
    <div class="front-brand">
      <div class="front-brand-dot"></div>
      <div class="front-brand-name">LARKWELL</div>
    </div>
    <h1 class="person-name">OWEN MARSH</h1>
    <div class="person-details">
      <span class="person-role">STORY MARKETING COACH</span>
      <span class="detail-divider"></span>
      <span class="person-email">owen@larkwellnow.com</span>
    </div>
  </section>

  <section class="card card-back">
    <div class="back-brand">
      <div class="back-brand-dot"></div>
      <div class="back-brand-name">LARKWELL</div>
      <div class="back-tagline">SHARE IDEAS THAT SPARK GROWTH</div>
    </div>
    <div class="back-divider"></div>
    <div class="offer">
      <p class="offer-headline">REACH MORE PEOPLE.<br>MAKE MORE MONEY.<br>CREATE MORE IMPACT.</p>
      <p class="offer-body">Get your free Larkwell<br>Starter Package and our<br>marketing guide today at</p>
      <p class="offer-link">Larkwellnow.com/start</p>
    </div>
    <div class="notes-box">
      <div class="notes-line first"></div>
      <div class="notes-line second"></div>
    </div>
  </section>
</main>
</body>
</html>
```